institute for female grief councelors needs a design for its facebook group

Each year about 350.000 German women do have a misscarriage while they are pregnant. Their pain and grief is soul deep. Lots of them are stay still in grief even if they have got other children who are healthy and alive. Lots of these women have got difficulty in finally letting go pain, rage and grief. Some are even still in grief after more than twenty or thirty years of having lost their child through misscarriage!!!!

With this facebook group I want to give hope, trust and support as well as helpful advice in coping with this deep soul pain after having lost your child through misscarriage.

The facebook cover shall cause a great curiosity and fascination to the mothers so that they are interested in joining our facebook group.

At our institute women can book a-one-year-training to become a certified "Coach for BirkenFeen" (grief councelor for women who are in deep grief after their misscarriage).

In Germany children who died through misscarriage are named "Sternenkind" (STARCHILD).
Therefore I want to have at least one shing star at the facebook cover symbolizing the still shining soullight of the dead child watching its mother who is still living on earth.

On the left side of the uploaded file you see the planet venus: symbol for mothers / female side of life.
The red sky colour symbolizes the colour of the uterus, the embryo's home before having died through misscarriage.
It ist also possible to include the silhoutte of a mother / several mothers looking up into the red / blue sky to watch the shining soullight of their dead child.

The facebook cover MUST include the following sentence:

Mama, ich lasse mein Licht für dich leuchten

(Mummy, I let my soullight shine for you)

Low design quality

Target Market(s)

German speaking mothers

Industry/Entity Type

coaching

Font styles to use
Script

Colors

Designer to choose colors to be used in the design.

Requirements
Must have
• golden fond writing, at least one shing star, silhouette of one / several mothers (no model typa - normal woman)
Nice to have
• planet venus - red background cover (like uterus colour)
Should not have
• mothers who like like a model or filmstar

```html
<!DOCTYPE html>
<html lang="de">
<head>
<meta charset="UTF-8">
<title>Sternenkind – Facebook Cover</title>
<link rel="stylesheet" href="https://fonts.googleapis.com/css2?family=Cookie&family=Montserrat:wght@700&display=swap">
<style>
  :root {
    --space-deep: #0d0a24;
    --space-violet: #3a1f5c;
    --nebula-red: #9b2a2f;
    --nebula-glow: #ffb38a;
    --venus-light: #f3dcae;
    --venus-mid: #d9b67c;
    --venus-shade: #8a6a45;
    --text-white: #ffffff;
    --gold: #b88a2c;
    --gold-light: #e0b95a;
    --button-bg: #ffffff;
  }
  html, body {
    margin: 0;
    padding: 0;
    overflow: hidden;
    background: var(--space-deep);
  }
  .cover {
    position: relative;
    width: 1200px;
    height: 676px;
    overflow: hidden;
  }
  .cover__sky {
    position: absolute;
    inset: 0;
    background:
      radial-gradient(circle at 958px 139px, rgba(255,240,220,0.95) 0, var(--nebula-glow) 30px, rgba(214,90,60,0.75) 110px, rgba(155,42,47,0.45) 260px, rgba(155,42,47,0) 460px),
      radial-gradient(ellipse 420px 260px at 1150px 380px, rgba(155,42,47,0.45), rgba(155,42,47,0)),
      radial-gradient(ellipse 500px 360px at 520px 180px, rgba(90,50,130,0.55), rgba(58,31,92,0)),
      linear-gradient(160deg, #17123a 0%, var(--space-violet) 45%, #2a1438 75%, var(--space-deep) 100%);
  }
  .cover__venus {
    position: absolute;
    left: 108px;
    top: 146px;
    width: 490px;
    height: 490px;
    border-radius: 50%;
    background:
      radial-gradient(circle at 40% 30%, var(--venus-light) 0, var(--venus-mid) 55%, var(--venus-shade) 100%);
  }
  .cover__sparkles {
    position: absolute;
    inset: 0;
  }
  .cover__headline {
    position: absolute;
    left: 640px;
    top: 170px;
    width: 470px;
    margin: 0;
    text-align: center;
    font-family: "Cookie", cursive;
    font-weight: 400;
    font-size: 78px;
    line-height: 84px;
    color: var(--text-white);
    text-shadow: 2px 3px 0 var(--gold);
  }
  .cover__headline .greeting {
    display: block;
    font-size: 70px;
  }
  .cover__cta {
    position: absolute;
    left: 757px;
    top: 532px;
    display: flex;
    align-items: center;
    gap: 8px;
  }
  .cover__heart {
    width: 40px;
    height: 36px;
  }
  .cover__button {
    display: inline-block;
    padding: 0 14px;
    height: 42px;
    line-height: 43px;
    background: var(--button-bg);
    border-radius: 8px;
    font-family: "Montserrat", sans-serif;
    font-weight: 700;
    font-size: 24px;
    color: var(--gold);
    text-decoration: none;
    letter-spacing: 0.2px;
  }
</style>
</head>
<body>
  <main class="cover">
    <div class="cover__sky" role="img" aria-label="Sternenhimmel mit violettem Nebel und rot leuchtender Sonne oben rechts"></div>
    <div class="cover__venus" role="img" aria-label="Planet Venus mit feiner Linienzeichnung einer Frau, die nach oben blickt"></div>

    <svg class="cover__sparkles" width="1200" height="676" viewBox="0 0 1200 676" aria-hidden="true">
      <defs>
        <radialGradient id="sparkle-glow">
          <stop offset="0" stop-color="#fff" stop-opacity="0.9"/>
          <stop offset="1" stop-color="#ffb060" stop-opacity="0"/>
        </radialGradient>
      </defs>
      <g fill="#ffffff">
        <circle cx="1054" cy="88" r="22" fill="url(#sparkle-glow)"/>
        <path d="M1054 48 Q1057 85 1094 88 Q1057 91 1054 128 Q1051 91 1014 88 Q1051 85 1054 48Z"/>
        <path d="M1105 93 Q1106 107 1120 108 Q1106 109 1105 123 Q1104 109 1090 108 Q1104 107 1105 93Z"/>
        <path d="M1088 52 Q1089 60 1097 61 Q1089 62 1088 70 Q1087 62 1079 61 Q1087 60 1088 52Z"/>
        <path d="M1099 128 Q1100 137 1109 138 Q1100 139 1099 148 Q1098 139 1089 138 Q1098 137 1099 128Z" fill="#ffd27a"/>
        <path d="M55 579 Q57 605 85 607 Q57 609 55 637 Q53 609 26 607 Q53 605 55 579Z"/>
        <path d="M95 614 Q96 624 107 625 Q96 626 95 637 Q94 626 83 625 Q94 624 95 614Z"/>
        <path d="M82 581 Q83 586 88 587 Q83 588 82 593 Q81 588 76 587 Q81 586 82 581Z"/>
      </g>
    </svg>

    <h1 class="cover__headline">
      <span class="greeting">Mama,</span>
      ich lasse mein<br>
      Licht für dich<br>
      leuchten
    </h1>

    <div class="cover__cta">
      <svg class="cover__heart" viewBox="0 0 40 36" aria-hidden="true">
        <defs>
          <linearGradient id="heart-gold" x1="0" y1="0" x2="1" y2="1">
            <stop offset="0" stop-color="#e8c563"/>
            <stop offset="0.5" stop-color="#c9982f"/>
            <stop offset="1" stop-color="#9c7420"/>
          </linearGradient>
        </defs>
        <path d="M20 34 C6 24 1 17 1 10 C1 4 6 1 11 1 C15 1 18 3 20 7 C22 3 25 1 29 1 C34 1 39 4 39 10 C39 17 34 24 20 34Z" fill="url(#heart-gold)"/>
      </svg>
      <a class="cover__button" href="#">JOIN NOW</a>
    </div>
  </main>
</body>
</html>
```